Bicycle Tour Schedule on a Business Card

Need to develop a 2 side business card that highlights a series of bike tours on 1 side and a series of events on the other side.
This will be inserted into a card wallet that attaches to a cell phone and will be handed out at an expo. The card wallets are black and red so color must coordinate with both. There is a photo of the card wallets attached.

1 side needs to be devoted to Pedal Vista Trek and the others to KQR Venture events on the other. Dates and websites are very important.

Target Market(s)

Cyclists
Predominantly men ages 40+
Educated, Professionals

Industry/Entity Type

Business

Font styles to use
Serif

Requirements
Must have
• Pedal vista treks logo on 1 side and KQR Venture logo on the other side
• dates and websites clearly visible
• Design of both sides must go together.
• Must be portrait not landscape

```html
<!DOCTYPE html>
<html lang="en">
<head>
<meta charset="utf-8">
<title>Pedal Vista Treks &amp; KQR Venture – Event Cards</title>
<link rel="stylesheet" href="https://fonts.googleapis.com/css2?family=Open+Sans:ital,wght@0,400;0,600;0,700;1,700&display=swap">
<style>
  :root {
    --backdrop: #8b8c8c;
    --card: #f1f1f1;
    --ink: #3a3a3a;
    --trek-blue: #0f4f9c;
    --trek-green: #3a9a48;
    --venture-red: #b3172c;
    --venture-teal: #1d6f8a;
  }
  * { box-sizing: border-box; margin: 0; padding: 0; }
  html, body {
    width: 1105px; height: 1200px; overflow: hidden;
    background: var(--backdrop);
    font-family: "Open Sans", Arial, sans-serif;
    color: var(--ink);
  }
  .stage { position: relative; width: 1105px; height: 1200px; }
  .card {
    position: absolute; top: 269px; width: 398px; height: 697px;
    background: var(--card);
    text-align: center;
  }
  .card--trek { left: 113px; }
  .card--venture { left: 597px; }
  .block { position: absolute; left: 0; right: 0; }
  .event-name { font-size: 18px; line-height: 24px; font-weight: 400; }
  .event-date { font-size: 18px; line-height: 24px; font-weight: 700; }
  .headline {
    font-size: 21px; line-height: 26px; font-weight: 700; font-style: italic;
  }
  .card--trek .headline { color: var(--trek-blue); }
  .card--venture .headline { color: var(--venture-red); }

  .brand { display: flex; align-items: center; justify-content: center; gap: 12px; }
  .brand-name { font-weight: 700; font-size: 34px; }
  .brand--trek .brand-name { color: var(--trek-green); }
  .brand-mark--trek { width: 22px; height: 22px; border-radius: 50%; background: var(--trek-blue); }
  .brand--venture { flex-direction: column; gap: 16px; }
  .brand-mark--venture { width: 110px; height: 110px; background: var(--venture-red); }
  .brand--venture .brand-name { color: var(--venture-teal); font-size: 30px; }

  .band-trek {
    position: absolute; left: 0; right: 0; bottom: 0; height: 24px;
    background: var(--trek-blue); border-top: 4px solid var(--trek-green);
  }
  .band-venture {
    position: absolute; left: 0; right: 0; bottom: 0; height: 24px;
    background: var(--venture-red);
  }
</style>
</head>
<body>
<main class="stage">

  <section class="card card--trek">
    <div class="block brand brand--trek" style="top:95px">
      <span class="brand-mark brand-mark--trek"></span>
      <span class="brand-name">Pedal Vista Treks</span>
    </div>
    <p class="block headline" style="top:246px">Fully supported bike tours.<br>Discover the hidden gems on<br>two wheels</p>
    <div class="block" style="top:364px">
      <p class="event-name">Heart of Colorado</p>
      <p class="event-date">June 26 - July 2, 2016</p>
    </div>
    <div class="block" style="top:432px">
      <p class="event-name">Colorado Front Range Tour</p>
      <p class="event-date">August 14-20, 2016</p>
    </div>
    <div class="block" style="top:500px">
      <p class="event-name">Cape Cod Tour</p>
      <p class="event-date">October 9 -15, 2016</p>
    </div>
    <div class="block" style="top:567px">
      <p class="event-name">Florida Key Tours</p>
      <p class="event-date">November 6-12, 2016 &amp;<br>December 4-10, 2016</p>
    </div>
    <div class="band-trek"></div>
  </section>

  <section class="card card--venture">
    <div class="block brand brand--venture" style="top:28px">
      <span class="brand-mark brand-mark--venture"></span>
      <span class="brand-name">KQR Venture</span>
    </div>
    <p class="block headline" style="top:232px">Trio Wheel Series:<br>Cycling camps for youth</p>
    <div class="block" style="top:302px">
      <p class="event-name">Mountain Bike Camp</p>
      <p class="event-date">July 8-10, 2016</p>
    </div>
    <div class="block" style="top:362px">
      <p class="event-name">Cyclocross Camp</p>
      <p class="event-date">August 26-28, 2016<br>Triowheelseries.org</p>
    </div>
    <div class="block" style="top:447px">
      <p class="event-name">Mile High Hundred Ride</p>
      <p class="event-date">June 18, 2016<br>Milehighhundred.com</p>
    </div>
    <div class="block" style="top:531px">
      <p class="event-name">Summit Loop Challenge</p>
      <p class="event-date">July 30, 2016 - Summitloopride.com</p>
    </div>
    <div class="block" style="top:589px">
      <p class="event-name">Goofy Spoke Ride</p>
      <p class="event-date">September 11, 2016<br>goofyspokeride.com</p>
    </div>
    <div class="band-venture"></div>
  </section>

</main>
</body>
</html>
```